Elmhollow Restaurnt Lunch Menu Redesign:

We have two lunch special menus that need to be reformatted into a 4.25inx11in and need a graphics design update. Some menu items need to change and some descriptions need to updated. This new menu should double sided with the Main Dining Lunch Menu on the front side and Teppanyaki Lunch menu on the back.

Both menus should follow the same design formatting as the main dining lunch menu (font, sizing, ect.)

```html
<!DOCTYPE html>
<html lang="en">
<head>
<meta charset="utf-8">
<title>Lunch Menus</title>
<link href="https://fonts.googleapis.com/css2?family=Marcellus&family=EB+Garamond:ital,wght@0,400;1,400&family=Libre+Baskerville:wght@700&display=swap" rel="stylesheet">
<style>
  :root {
    --backdrop: #ececec;
    --paper: #fffbe8;
    --band: #b08f52;
    --rule: #b08f52;
    --navy: #1d4c8a;
    --gold-text: #ab8a4e;
    --ink: #5a5a5a;
    --white: #ffffff;
  }
  * { margin: 0; padding: 0; box-sizing: border-box; }
  html, body { width: 1200px; height: 709px; overflow: hidden; background: var(--backdrop); }
  .spread { position: relative; width: 1200px; height: 709px; display: flex; justify-content: center; align-items: center; gap: 60px; }
  .menu-card {
    position: relative; width: 246px; height: 637px; background: var(--paper);
    box-shadow: 0 2px 6px rgba(0,0,0,0.18);
    font-family: "EB Garamond", serif; color: var(--ink);
  }
  .menu-band {
    height: 45px; background: var(--band); color: var(--white);
    font-family: "Marcellus", serif; font-size: 25px; line-height: 45px; text-align: center;
  }
  .menu-frame {
    position: absolute; left: 8px; right: 8px; top: 45px; bottom: 7px;
    border: 1px solid var(--rule); border-top: none; border-radius: 0 0 20px 20px;
    pointer-events: none;
  }
  .menu-body { position: relative; padding: 1px 20px 0 14px; }
  .hours { text-align: center; color: var(--gold-text); font-size: 11px; line-height: 12px; }
  .section-title {
    text-align: center; color: var(--navy); font-family: "Marcellus", serif;
    font-size: 17px; line-height: 17px; margin-top: 12px; font-weight: 700; -webkit-text-stroke: 0.3px var(--navy);
  }
  .section-note { text-align: center; color: var(--gold-text); font-size: 9.5px; line-height: 10px; }
  .section-note.plain { color: var(--ink); }
  .price { font-family: "Libre Baskerville", serif; font-weight: 700; color: var(--navy); font-size: 9.5px; white-space: nowrap; }
  .dish-list { list-style: none; margin-top: 6px; }
  .dish-list li { display: flex; justify-content: space-between; align-items: center; height: 19.3px; font-size: 10px; }
  .dish-list.kids { margin-top: 9px; }
  .ages { margin-top: 2px; text-align: center; color: var(--gold-text); font-size: 11px; line-height: 12px; }

  .combo { display: flex; justify-content: space-between; align-items: flex-end; font-size: 10px; line-height: 10.5px; margin-bottom: 2.5px; }
  .combo.top { align-items: flex-start; }
  .combo .desc { max-width: 180px; }
  .sandwiches { margin-top: 12px; }
  .tight { margin-top: 6px; }
  .fish-list { list-style: none; text-align: center; font-size: 9.5px; line-height: 11.3px; }
  .course-list { list-style: none; }
  .course-list li { display: flex; justify-content: space-between; font-size: 10px; line-height: 13px; }
  .course-list li.short { line-height: 10.5px; }
  .course-list li.stack { line-height: 9.5px; align-items: flex-start; }
  .course-list .variant { font-style: italic; font-size: 9px; line-height: 10.5px; }
  .meals-note { text-align: center; font-size: 10px; line-height: 10.5px; }
  .raw-note { text-align: center; font-size: 9.5px; line-height: 10.5px; }
</style>
</head>
<body>
<main class="spread">

  <section class="menu-card" aria-label="Teppanyaki lunch menu">
    <h1 class="menu-band">Teppanyaki Lunch</h1>
    <div class="menu-frame"></div>
    <div class="menu-body">
      <p class="hours">(Available until 11.00 am-2:30 pm)</p>
      <h2 class="section-title">Served</h2>
      <p class="section-note">with Miso Soup or Salad,<br>Choice of Rice &amp; Vegetables</p>
      <ul class="dish-list">
        <li><span>Hibachi Chicken</span><span class="price">$18.00</span></li>
        <li><span>Hibachi Shrimp</span><span class="price">$19.00</span></li>
        <li><span>Hibachi New York Steak</span><span class="price">$20.00</span></li>
        <li><span>Hibachi Salmon</span><span class="price">$20.00</span></li>
        <li><span>Teriyaki Beef</span><span class="price">$19.00</span></li>
        <li><span>Hibachi Scallop</span><span class="price">$20.00</span></li>
        <li><span>Chicken and Shrimp</span><span class="price">$21.00</span></li>
        <li><span>Scallop and Shrimp</span><span class="price">$22.00</span></li>
        <li><span>New York Steak and Chicken</span><span class="price">$22.00</span></li>
        <li><span>New York Steak and Shrimp</span><span class="price">$23.00</span></li>
        <li><span>New York Steak and Scallop</span><span class="price">$24.00</span></li>
        <li><span>Filet Mignon</span><span class="price">$23.00</span></li>
        <li><span>Filet Mignon and Chicken</span><span class="price">$25.00</span></li>
        <li><span>Filet Mignon and Shrimp</span><span class="price">$26.00</span></li>
        <li><span>Filet Mignon and Scallop</span><span class="price">$27.00</span></li>
      </ul>
      <h2 class="section-title">Special Menu</h2>
      <p class="ages">Ages 12 and Under ~ Ages 65 and Older</p>
      <p class="section-note plain">Served with Miso Soup or Salad,<br>Choice of Rice &amp; Vegetables</p>
      <ul class="dish-list kids">
        <li><span>Hibachi Chicken</span><span class="price">$15.00</span></li>
        <li><span>Hibachi Shrimp</span><span class="price">$16.00</span></li>
        <li><span>Hibachi Scallop</span><span class="price">$08.00</span></li>
        <li><span>Steak</span><span class="price">$08.00</span></li>
        <li><span>Hibachi Scallop</span><span class="price">$08.00</span></li>
        <li><span>Teriyaki Beef</span><span class="price">$16.00</span></li>
      </ul>
    </div>
  </section>

  <section class="menu-card" aria-label="Lunch specials menu">
    <h1 class="menu-band">Lunch Specials</h1>
    <div class="menu-frame"></div>
    <div class="menu-body">
      <p class="hours">(Served Daily 11.00 am - 3.00 pm)</p>
      <h2 class="section-title">Sandwiches</h2>
      <p class="section-note">Served with Choice of Miso Soup or<br>House Salad &amp; Potato Chips</p>
      <div class="sandwiches">
        <div class="combo"><span class="desc">Fried Breaded Calamari Steak with Tomato, Lettuce &amp; Onion</span><span class="price">$16.00</span></div>
        <div class="combo"><span class="desc">Grilled Chicken with Bacon, Tomato, Lettuce &amp; Mayonnaise Drizzle</span><span class="price">$16.00</span></div>
        <div class="combo"><span class="desc">Hamburger with Lettuce, Tomato, Onion, Mayonnaise Drizzle</span><span class="price">$18.00</span></div>
        <div class="combo"><span class="desc">Fried Soft Shell Crab Burger with Avocado, Lettuce, Tomato, Onion &amp; Mayo</span><span class="price">$20.00</span></div>
      </div>
      <h2 class="section-title tight">Sushi Specials</h2>
      <div class="combo top"><span class="desc">Please Select 4 of the followings for Served with a 4 piece California Roll &amp; Miso Soup or</span><span class="price">$16.00</span></div>
      <h2 class="section-title tight">House Salad</h2>
      <ul class="fish-list">
        <li>*Hamachi - Yellowtail Tuna</li>
        <li>*Maguro - Yellow fin Tuna</li>
        <li>*Hotate - Scallop *Smoked Salmon *Ika - Squid</li>
        <li>*Ikura - Salmon Roe Tako - Octopus</li>
        <li>*Saba - Mackerel Unagi - BBQ Eel</li>
        <li>*Sake - Salmon Ebi - Shrimp</li>
        <li>*Tai - Red Snapper Tamago - Egg</li>
      </ul>
      <h2 class="section-title tight">Main Courses</h2>
      <p class="section-note" style="line-height:10.5px">Served with Rice &amp; Choice of Miso Soup<br>or House Salad</p>
      <p class="meals-note">All Meals Served with Rice.</p>
      <ul class="course-list">
        <li class="short"><span>Upgrade to fried rice for only</span><span class="price">$04.00</span></li>
        <li><span>Organic Tofu Teriyaki</span><span class="price">$14.00</span></li>
        <li class="variant"><span>- Served Grilled or Tempura Fried</span></li>
        <li><span>Chicken Teriyaki</span><span class="price">$16.00</span></li>
        <li><span>Spicy Chicken Teriyaki</span><span class="price">$16.00</span></li>
        <li><span>Beef Teriyaki</span><span class="price">$16.00</span></li>
        <li><span>Spicy Beef Teriyaki</span><span class="price">$16.00</span></li>
        <li class="stack"><span>Chicken Katsu -Breaded Chicken Breast<br>Katsu Don - Fried Chicken Breast,</span><span class="price">$15.00</span></li>
        <li><span>Egg &amp; Onion over Rice</span><span class="price">$16.00</span></li>
        <li><span>Unagi Don - BBQ Eel over Rice</span><span class="price">$19.00</span></li>
        <li><span>Shrimp &amp; Vegetable Tempura</span><span class="price">$16.00</span></li>
      </ul>
      <h2 class="section-title tight">*Served Raw</h2>
      <p class="raw-note">20% gratuity added to parties of 6 or more.<br>Consuming raw or undercooked food may<br>increase your risk of foodborne illness</p>
    </div>
  </section>

</main>
</body>
</html>
```